Automotive eCommerce Business looking for a business card design

Looking for a clean and simple business card design. Our company name is "Brindle Auto" and we are a company specializing in the ecommerce sales of automotive parts, specifically for pick up trucks and large SUVs. Our company colours are red, black, and white.

Feel free to use the logo provided or create a new logo that you seem fit. Looking forward to your creative ideas!

Industry/Entity Type

Automotive

Contact Information for Business Card

We were thinking of a possibly two-sided design featuring just the logo and company name on one side, and personal information on the other side. Single sided designs will be considered as well.

Font styles to use
Serif
Sans Serif
Decorative

Colors
ec1f27
ffffff
000000

Requirements
Must have
• Space for employee's name, title, phone number and email address, along with the company address and website somewhere.

```html
<!DOCTYPE html>
<html lang="en">
<head>
<meta charset="utf-8">
<title>Brindle Auto Ltd — Business Card</title>
<link rel="stylesheet" href="https://fonts.googleapis.com/css2?family=Work+Sans:wght@400;500;600&display=swap">
<style>
  :root {
    --red: #ec1f27;
    --black: #000000;
    --white: #ffffff;
    --backdrop: #2e2e2e;
  }
  * { margin: 0; padding: 0; box-sizing: border-box; }
  html, body {
    width: 1200px; height: 900px; overflow: hidden;
    background: var(--backdrop);
    font-family: "Work Sans", Arial, sans-serif;
  }
  .card {
    position: absolute;
    left: 280px;
    width: 640px; height: 366px;
    border-radius: 22px;
    overflow: hidden;
  }
  .card--back { top: 50px; background: var(--black); }
  .card--front { top: 466px; background: var(--white); }

  .wordmark {
    position: absolute;
    display: flex; align-items: center; gap: 12px;
    font-weight: 600; letter-spacing: 0.5px; white-space: nowrap;
  }
  .wordmark__dot { width: 14px; height: 14px; border-radius: 50%; background: var(--red); }
  .card--back .wordmark { left: 0; right: 0; justify-content: center; top: 130px; font-size: 44px; color: var(--white); }
  .card--front .wordmark { left: 44px; top: 50px; font-size: 36px; color: var(--black); }

  .back-url {
    position: absolute; left: 0; right: 0; top: 236px;
    text-align: center; font-size: 17px; color: var(--white); letter-spacing: 0.4px;
  }
  .accent { color: var(--red); }

  .wave { position: absolute; inset: 0; width: 640px; height: 366px; }

  .person {
    position: absolute; right: 56px; top: 228px;
    text-align: right; color: var(--white);
  }
  .person__name { font-size: 21px; font-weight: 500; letter-spacing: 2px; color: var(--red); line-height: 1.1; }
  .person__title { font-size: 14px; margin-top: 3px; }

  .contact {
    position: absolute; right: 28px; top: 278px;
    list-style: none; color: var(--white); font-size: 13.5px;
  }
  .contact li { display: flex; justify-content: flex-end; align-items: center; gap: 14px; height: 18px; white-space: nowrap; }
  .contact svg { width: 13px; height: 13px; flex: none; fill: none; stroke: var(--red); stroke-width: 1.8; }
</style>
</head>
<body>

<section class="card card--back" aria-label="Card back">
  <div class="wordmark"><span class="wordmark__dot"></span>Brindle Auto Ltd</div>
  <p class="back-url">www.<span class="accent">brindleautoltd</span>.com</p>
</section>

<section class="card card--front" aria-label="Card front">
  <svg class="wave" viewBox="0 0 640 366" aria-hidden="true">
    <g transform="translate(0,-34)">
      <path d="M0,120 C4,190 70,232 200,258 C90,246 20,200 0,150 Z" fill="var(--black)"/>
      <path d="M0,172 C60,250 200,252 340,234 C450,218 540,190 640,164 L640,177 C540,203 450,231 340,247 C200,266 60,262 0,192 Z" fill="var(--red)"/>
      <path d="M0,202 C60,272 200,276 340,258 C450,243 540,214 640,188 L640,400 L0,400 Z" fill="var(--black)"/>
      <path d="M470,226 C560,228 620,262 640,320 L640,282 C610,244 550,228 470,226 Z" fill="var(--red)"/>
      <path d="M455,222 C550,222 615,254 640,310 L640,318 C615,262 552,228 455,222 Z" fill="var(--white)"/>
    </g>
  </svg>

  <div class="wordmark"><span class="wordmark__dot"></span>Brindle Auto Ltd</div>

  <div class="person">
    <p class="person__name">OWEN HALVORSEN</p>
    <p class="person__title">Director</p>
  </div>

  <ul class="contact">
    <li><span>555.014.2325</span>
      <svg viewBox="0 0 14 14"><path d="M3 1.5 L5.5 4 L4 5.5 C5 7.5 6.5 9 8.5 10 L10 8.5 L12.5 11 L11 12.5 C6 12 2 8 1.5 3 Z"/></svg></li>
    <li><span>555.019.5887</span>
      <svg viewBox="0 0 14 14"><rect x="3.5" y="1" width="7" height="12" rx="1.2"/><path d="M6 11h2"/></svg></li>
    <li><span>info@brindleautoltd.com</span>
      <svg viewBox="0 0 14 14"><rect x="1" y="3" width="12" height="8" rx="1"/><path d="M1 3.5 L7 8 L13 3.5"/></svg></li>
    <li><span>www.<span class="accent">brindleautoltd</span>.com</span>
      <svg viewBox="0 0 14 14"><circle cx="7" cy="7" r="5.8"/><ellipse cx="7" cy="7" rx="2.5" ry="5.8"/><path d="M1.2 7h11.6"/></svg></li>
  </ul>
</section>

</body>
</html>
```